Business cards for Harbourline Supply Pty Ltd that import building products into Australia from China
Target Market(s)
Business to Business
Industry/Entity Type
Business
Contact Information for Business Card
Front: Logo and Business Name
Rear:
Desmond Varrick
General Manager
Mobile: 0427 561 394
email: dessie@harbourlinesupply.com.au
alternative email: dessie@outbackworks.com.au
web: www.harbourlinesupply.com.au
Adelaide, Brisbane and Darwin
Colors
ec1f27
fbee3d

```html
<!DOCTYPE html>
<html lang="en">
<head>
<meta charset="utf-8">
<title>Harbourline Supply Pty Ltd — Business Cards</title>
<link rel="stylesheet" href="https://fonts.googleapis.com/css2?family=Montserrat:wght@400;500;600;700&display=swap">
<style>
  :root {
    --red: #ec1f27;
    --yellow: #fbee3d;
    --ink: #0a0a0b;
    --paper: #ffffff;
    --grey-text: #333333;
    --backdrop: #3a3a3c;
    --white: #ffffff;
  }
  * { margin: 0; padding: 0; box-sizing: border-box; }
  html, body {
    width: 1200px; height: 864px; overflow: hidden;
    background: var(--backdrop);
    font-family: "Montserrat", sans-serif;
  }
  .sheet {
    width: 1200px; height: 864px;
    display: flex; align-items: center; justify-content: center; gap: 40px;
  }
  .card {
    width: 540px; height: 330px;
    border-radius: 18px;
    position: relative;
    overflow: hidden;
  }
  /* Front */
  .card--front { background: var(--paper); }
  .brand {
    display: flex; align-items: center; gap: 14px;
    color: var(--red); font-weight: 700; text-transform: uppercase;
    letter-spacing: 0.02em;
  }
  .brand__mark { width: 30px; height: 30px; background: var(--red); flex: none; }
  .brand__name { font-size: 28px; line-height: 1.05; }
  .card--front .brand {
    position: absolute; left: 0; right: 0; top: 118px; justify-content: center;
  }
  .locations {
    position: absolute; left: 0; right: 0; bottom: 58px;
    text-align: center; font-size: 15px; color: var(--grey-text); font-weight: 500;
  }
  .locations .dot { color: var(--red); margin: 0 6px; }

  /* Back */
  .card--back { background: var(--ink); color: var(--white); }
  .card--back .brand {
    position: absolute; left: 36px; top: 146px; width: 236px;
  }
  .card--back .brand__mark { background: var(--yellow); width: 22px; height: 22px; }
  .card--back .brand__name { font-size: 21px; }
  .divider {
    position: absolute; left: 292px; top: 86px; width: 1.5px; height: 160px;
    background: var(--red);
  }
  .contact { position: absolute; left: 312px; top: 92px; right: 14px; }
  .contact__name { color: var(--red); font-weight: 700; font-size: 21px; }
  .contact__role { font-size: 13.5px; font-weight: 500; margin-top: 2px; margin-bottom: 16px; }
  .contact__list { list-style: none; }
  .contact__item {
    display: flex; align-items: center; gap: 8px;
    font-size: 11.5px; font-weight: 500; margin-bottom: 6px; white-space: nowrap;
  }
  .contact__item svg { width: 13px; height: 13px; flex: none; }
</style>
</head>
<body>
<main class="sheet">
  <section class="card card--front" aria-label="Card front">
    <div class="brand">
      <span class="brand__mark"></span>
      <span class="brand__name">Harbourline<br>Supply Pty Ltd</span>
    </div>
    <p class="locations">Adelaide<span class="dot">•</span>Brisbane<span class="dot">•</span>Darwin</p>
  </section>

  <section class="card card--back" aria-label="Card back">
    <div class="brand">
      <span class="brand__mark"></span>
      <span class="brand__name">Harbourline<br>Supply Pty Ltd</span>
    </div>
    <div class="divider"></div>
    <div class="contact">
      <p class="contact__name">Desmond Varrick</p>
      <p class="contact__role">General Manager</p>
      <ul class="contact__list">
        <li class="contact__item">
          <svg viewBox="0 0 14 14" fill="none" stroke="#fbee3d" stroke-width="1.4"><rect x="3.5" y="1" width="7" height="12" rx="1.2"/><line x1="6" y1="11" x2="8" y2="11"/></svg>
          0427 561 394
        </li>
        <li class="contact__item">
          <svg viewBox="0 0 14 14"><rect x="1" y="3" width="12" height="8" fill="#fbee3d"/><path d="M1 3 L7 8 L13 3" fill="none" stroke="#0a0a0b" stroke-width="1.2"/></svg>
          dessie@harbourlinesupply.com.au
        </li>
        <li class="contact__item">
          <svg viewBox="0 0 14 14"><rect x="1" y="3" width="12" height="8" fill="#fbee3d"/><path d="M1 3 L7 8 L13 3" fill="none" stroke="#0a0a0b" stroke-width="1.2"/></svg>
          dessie@outbackworks.com.au
        </li>
        <li class="contact__item">
          <svg viewBox="0 0 14 14" fill="none" stroke="#fbee3d" stroke-width="1.2"><circle cx="7" cy="7" r="5.8"/><ellipse cx="7" cy="7" rx="2.6" ry="5.8"/><line x1="1.2" y1="7" x2="12.8" y2="7"/></svg>
          www.harbourlinesupply.com.au
        </li>
      </ul>
    </div>
  </section>
</main>
</body>
</html>
```